Design a compelling Tarnwove Business Card that will drive people to my site

I want a business card that I can give to people—less to tell them who I am and more to direct them to my website. My website is a portal for Pelmor Aquatics Officials and a place for people who want to become Pelmor Aquatics Officials.
I am uploading my official company logo as well as a business card mockup that I did on my own. Please feel free to completely stray from this design.
I've included a screen recording of the homepage of my website as well.
Target Market(s)
Pelmor Aquatics Officials and people who desire to become one
Contact Information for Business Card
website url
Look and feel
Each slider illustrates characteristics of the customer's brand and the style your logo design should communicate.

```html
<!DOCTYPE html>
<html lang="en">
<head>
<meta charset="utf-8">
<title>Tarnwove Business Card</title>
<link href="https://fonts.googleapis.com/css2?family=Montserrat:wght@400;500;700;800&display=swap" rel="stylesheet">
<style>
  :root {
    --page-bg: #3b3b3d;
    --brand-blue: #3a55a8;
    --brand-blue-deep: #2f4797;
    --accent-light: #9aaee0;
    --card-white: #ffffff;
    --text-dark: #2a2a2e;
    --wordmark-white: #ffffff;
  }
  * { box-sizing: border-box; margin: 0; padding: 0; }
  html, body {
    width: 1200px;
    height: 915px;
    overflow: hidden;
    background: var(--page-bg);
    font-family: "Montserrat", sans-serif;
  }
  .canvas {
    position: relative;
    width: 1200px;
    height: 915px;
  }
  .card {
    position: absolute;
    left: 250px;
    width: 700px;
    height: 400px;
    border-radius: 26px;
    overflow: hidden;
  }
  .card--front {
    top: 40px;
    background: var(--brand-blue);
  }
  .card--back {
    top: 475px;
    background: var(--card-white);
  }
  .bubble-field {
    position: absolute;
    inset: 0;
    background:
      radial-gradient(circle at 78% 22%, rgba(255,255,255,0.16) 0, rgba(255,255,255,0) 22%),
      radial-gradient(circle at 22% 70%, rgba(255,255,255,0.10) 0, rgba(255,255,255,0) 28%),
      linear-gradient(135deg, var(--brand-blue) 0%, var(--brand-blue-deep) 100%);
  }
  .front-wordmark {
    position: absolute;
    left: 0;
    right: 0;
    top: 150px;
    display: flex;
    align-items: center;
    justify-content: center;
    gap: 18px;
  }
  .front-wordmark .mark-dot {
    width: 34px;
    height: 34px;
    border-radius: 50%;
    background: var(--wordmark-white);
  }
  .front-wordmark .name {
    font-weight: 700;
    font-size: 84px;
    letter-spacing: -1px;
    color: var(--wordmark-white);
  }
  .back-wordmark {
    position: absolute;
    left: 46px;
    top: 90px;
    display: flex;
    align-items: center;
    gap: 12px;
  }
  .back-wordmark .mark-dot {
    width: 22px;
    height: 22px;
    border-radius: 50%;
    background: var(--brand-blue);
  }
  .back-wordmark .name {
    font-weight: 700;
    font-size: 54px;
    letter-spacing: -1px;
    color: var(--brand-blue);
  }
  .holder {
    position: absolute;
    right: 40px;
    top: 44px;
    text-align: right;
  }
  .holder .person {
    font-weight: 800;
    font-size: 26px;
    color: var(--brand-blue);
  }
  .holder .role {
    font-weight: 500;
    font-size: 17px;
    color: var(--text-dark);
    margin-top: 2px;
  }
  .edge-tab {
    position: absolute;
    right: 0;
    top: 40px;
    width: 26px;
    height: 46px;
    background: var(--accent-light);
  }
  .contact-list {
    position: absolute;
    left: 46px;
    bottom: 48px;
    list-style: none;
  }
  .contact-list li {
    display: flex;
    align-items: center;
    gap: 12px;
    font-size: 19px;
    color: var(--text-dark);
    line-height: 1.7;
  }
  .contact-list svg {
    width: 18px;
    height: 18px;
    fill: var(--brand-blue);
    flex: none;
  }
</style>
</head>
<body>
<main class="canvas">
  <section class="card card--front">
    <div class="bubble-field" role="img" aria-label="Soft pattern of translucent bubbles across the blue card"></div>
    <div class="front-wordmark">
      <span class="mark-dot"></span>
      <span class="name">Tarnwove</span>
    </div>
  </section>

  <section class="card card--back">
    <div class="edge-tab"></div>
    <div class="holder">
      <p class="person">Martin Holloway</p>
      <p class="role">CEO &amp; Founder</p>
    </div>
    <div class="back-wordmark">
      <span class="mark-dot"></span>
      <span class="name">Tarnwove</span>
    </div>
    <ul class="contact-list">
      <li>
        <svg viewBox="0 0 24 24" aria-hidden="true"><path d="M6.6 10.8a15.1 15.1 0 0 0 6.6 6.6l2.2-2.2a1 1 0 0 1 1-.25 11.4 11.4 0 0 0 3.6.57 1 1 0 0 1 1 1V20a1 1 0 0 1-1 1A17 17 0 0 1 3 4a1 1 0 0 1 1-1h3.5a1 1 0 0 1 1 1c0 1.25.2 2.45.57 3.57a1 1 0 0 1-.25 1z"/></svg>
        (555) 201-4478
      </li>
      <li>
        <svg viewBox="0 0 24 24" aria-hidden="true"><path d="M2 5h20v14H2z M2 5l10 8 10-8" /></svg>
        martin@tarnwove.com
      </li>
      <li>
        <svg viewBox="0 0 24 24" aria-hidden="true"><circle cx="12" cy="12" r="10"/><path d="M2 12h20M12 2c3 3 3 17 0 20M12 2c-3 3-3 17 0 20" stroke="#fff" stroke-width="1.4" fill="none"/></svg>
        www.tarnwove.com
      </li>
    </ul>
  </section>
</main>
</body>
</html>
```